Global Beard Oil Review Business needs a refresh

topwhiskertonic.net is a global business who's mission is to curate all available beard oils from around the world, review and grade them and present this curated collection to the user of the website.

The scope of this job includes the web site design and the design of a suitable logo to be used in the site header.

The existing site can be seen on http://topwhiskertonic.net, however this is a mock-up only the style and logo should NOT be used. This is to give you an idea of the concept of the site only.

This job is for PSD design only.

See attached design brief for detailed design requirements.
Updates

Project Deadline Extended
Reason: Extending deadline by 5 days to allow for final submissions

Target Market(s)

Men's grooming / retail

Industry/Entity Type

Retail

Number of Pages Required

2 page

Font styles to use
Sans Serif

Requirements
Must have
• 1) Comparison Table
• 2) Side Bar
• 3) Header area
• 4) Photo of Delvin Marsk (attached - can be circular or "cut-out")
• 5) Cool beard-oriented custom design background (e.g., stylistic black/brown on brown/orange beard background. I envision this beard background "drawing" rather than photo based)
• (see attached design requirements for details)
Nice to have
• Signature style writing at top with name "Delvin Marsk"
Should not have
• Do NOT use the look & feel or logo from the existing site.

```html
<!DOCTYPE html>
<html lang="en">
<head>
<meta charset="utf-8">
<title>Top Whisker Tonic</title>
<link href="https://fonts.googleapis.com/css2?family=Mouse+Memoirs&family=Raleway:wght@400;500;600;700&display=swap" rel="stylesheet">
<style>
:root{
  --orange:#f7a400;
  --maroon:#6b0f0f;
  --ink:#3a1d14;
  --text:#333;
  --grey-bg:#e4e4e4;
  --line:#e2e2e2;
  --white:#fff;
}
*{box-sizing:border-box;margin:0;padding:0}
html,body{width:1200px;height:2557px;overflow:hidden}
body{position:relative;font-family:"Raleway",sans-serif;color:var(--text);background:var(--grey-bg)}
.backdrop{position:absolute;inset:0;background:linear-gradient(135deg,#efefef,#d6d6d6 50%,#ececec)}
.display{font-family:"Mouse Memoirs",sans-serif;font-weight:400}

/* header */
.brand{position:absolute;left:77px;top:34px;display:flex;align-items:center;gap:12px}
.brand-dot{width:46px;height:46px;border-radius:50%;background:var(--orange)}
.brand-name{font-family:"Raleway",sans-serif;font-weight:700;font-size:26px;color:var(--ink);line-height:1}
.contact{position:absolute;left:740px;top:26px;display:flex;align-items:center;gap:10px;font-size:15px;color:var(--ink);white-space:nowrap}
.contact-icon{width:36px;height:36px;border-radius:50%;background:var(--orange);display:flex;align-items:center;justify-content:center;flex:none}
.social{position:absolute;top:30px;left:1004px;display:flex;gap:8px}
.social span{width:26px;height:26px;border-radius:50%;background:var(--orange);display:block}
.nav{position:absolute;top:85px;left:530px;display:flex;align-items:center;font-size:16px;color:var(--ink)}
.nav a{color:inherit;text-decoration:none;padding:4px 8px}
.nav .active{background:var(--maroon);color:var(--white);padding:5px 12px}
.nav .dot{width:4px;height:4px;border-radius:50%;background:var(--ink);margin:0 10px}

/* panel */
.panel{position:absolute;left:58px;top:127px;width:1084px;height:2390px;background:var(--white)}
.hero{position:absolute;left:68px;top:136px;width:1064px;height:409px;background:linear-gradient(90deg,#3a6f86,#6fb7cf 45%,#4d93ad 75%,#2f6b83)}
.hero-badge{position:absolute;left:300px;top:70px;width:300px;height:280px;border-radius:50%;background:rgba(255,255,255,.82);display:flex;flex-direction:column;align-items:center;justify-content:center;gap:14px}
.hero-badge .badge-name{font-weight:700;font-size:22px;color:var(--ink)}
.hero-badge .badge-with{font-weight:600;font-size:20px;color:var(--ink)}
.hero-title{position:absolute;left:617px;top:90px;font-size:62px;line-height:1.18;color:#151515;white-space:nowrap}
.hero-btn{position:absolute;left:617px;top:270px;width:143px;height:54px;background:var(--orange);color:var(--ink);font-family:"Raleway",sans-serif;font-weight:500;font-size:22px;display:flex;align-items:center;justify-content:center}
.hero-dots{position:absolute;left:623px;top:342px;display:flex;gap:6px}
.hero-dots span{width:7px;height:7px;border-radius:50%;background:rgba(255,255,255,.7)}
.hero-dots span.on{background:var(--orange)}

/* welcome */
.welcome{position:absolute;left:0;top:572px;width:1200px;text-align:center;font-size:64px;color:var(--ink)}
.welcome em{font-style:normal;color:var(--maroon)}
.intro{position:absolute;left:158px;top:650px;width:884px;text-align:center;font-size:12.5px;line-height:22px;color:#2a2a2a}

/* process */
.process{position:absolute;left:0;top:780px;width:1200px;height:170px}
.connectors{position:absolute;left:0;top:0}
.step{position:absolute;top:0;width:110px;text-align:center}
.step-circle{width:110px;height:110px;border-radius:50%;background:var(--orange);display:flex;align-items:center;justify-content:center}
.step-circle svg{display:block}
.step-label{margin-top:18px;font-size:30px;color:var(--ink);white-space:nowrap;margin-left:-40px;width:190px}

/* table */
.reviews{position:absolute;left:80px;top:987px;width:781px;border-collapse:collapse;table-layout:fixed;font-size:12px}
.reviews th{height:60px;font-weight:700;font-size:12.5px;text-align:center;padding:0 4px}
.reviews th.dark{background:var(--maroon);color:var(--orange)}
.reviews th.light{background:var(--orange);color:var(--maroon)}
.reviews td{height:91px;border:1px solid var(--line);vertical-align:top;padding-top:26px;text-align:center;color:#222}
.reviews td.product{text-align:left;padding:10px 6px}
.product-cell{display:flex;gap:8px;align-items:flex-start}
.thumb{width:40px;height:52px;flex:none;background:linear-gradient(#f3d27a,#c58a1a);border-radius:2px}
.thumb.dark{width:26px;margin:0 7px;background:linear-gradient(#8a4a2a,#4a1f10);border-radius:6px 6px 3px 3px}
.p-name{font-weight:700;font-size:15px;color:var(--maroon);line-height:1.2;margin-top:10px}
.p-maker{font-size:13px;color:#333;margin-top:3px}
.buy{display:inline-block;background:var(--orange);color:var(--white);font-size:12.5px;font-weight:600;padding:6px 8px}
.loading{position:absolute;left:394px;top:2441px;width:151px;height:34px;background:#c9c9c9;color:var(--white);font-size:14px;display:flex;align-items:center;justify-content:center;gap:6px}

/* sidebar */
.signup-box{position:absolute;left:885px;top:987px;width:235px;height:341px;background:var(--orange);text-align:center;padding:22px 16px}
.signup-box h3{font-size:33px;line-height:1.1;color:var(--maroon)}
.signup-box p{font-size:12.5px;line-height:1.5;color:var(--ink);margin-top:18px}
.signup-input{margin-top:18px;height:36px;background:var(--white);color:#999;font-size:12px;display:flex;align-items:center;justify-content:center}
.signup-btn{margin-top:12px;height:36px;background:var(--maroon);color:var(--white);font-weight:700;font-size:14px;display:flex;align-items:center;justify-content:center}
.signup-note{font-size:10.5px!important;color:#7a3a10!important;margin-top:22px!important}
.blog-heading{position:absolute;left:887px;top:1378px;font-size:40px;color:var(--maroon)}
.post{position:absolute;left:885px;width:235px}
.post-img{height:157px;border-radius:3px}
.post-title{margin-top:16px;font-weight:700;font-size:15px;color:var(--orange)}
.post-date{margin-top:8px;font-size:13px;color:#222}

/* footer */
.footer{position:absolute;left:0;top:2517px;width:1200px;height:40px;background:var(--orange);display:flex;align-items:center;justify-content:space-between;padding:0 80px;font-size:13px;color:var(--white)}
.footer-social{display:flex;gap:10px}
.footer-social span{width:26px;height:26px;border-radius:50%;border:2px solid var(--white);display:block}
</style>
</head>
<body>
<div class="backdrop" role="img" aria-label="Light grey background pattern of drawn bearded faces"></div>

<header>
  <div class="brand"><span class="brand-dot"></span><span class="brand-name">Top Whisker Tonic</span></div>
  <div class="contact">
    <span class="contact-icon"><svg width="18" height="18" viewBox="0 0 24 24"><path d="M6.6 10.8a15 15 0 0 0 6.6 6.6l2.2-2.2c.3-.3.7-.4 1-.2 1.1.4 2.3.6 3.6.6.6 0 1 .4 1 1V20c0 .6-.4 1-1 1A17 17 0 0 1 3 4c0-.6.4-1 1-1h3.5c.6 0 1 .4 1 1 0 1.3.2 2.5.6 3.6.1.3 0 .7-.2 1z" fill="#6b0f0f"/></svg></span>
    <span>info@topwhiskertonic.net</span>
  </div>
  <div class="social"><span></span><span></span><span></span><span></span></div>
  <nav class="nav">
    <a class="active">Home</a>
    <a>About</a><span class="dot"></span>
    <a>Our Charter</a><span class="dot"></span>
    <a>Beard Oil Review Methodology</a><span class="dot"></span>
    <a>Blog</a>
  </nav>
</header>

<div class="panel"></div>

<section class="hero" role="img" aria-label="Photo of Delvin Marsk giving a thumbs up and holding a beard oil bottle in front of a blue wooden wall">
  <div class="hero-badge"><span class="badge-name">Top Whisker Tonic</span><span class="badge-with">with Delvin Marsk</span></div>
  <h1 class="hero-title display">Curate, Review &amp; Grade<br>Then Present</h1>
  <div class="hero-btn">See Table</div>
  <div class="hero-dots"><span></span><span></span><span></span><span class="on"></span></div>
</section>

<h2 class="welcome display">Welcome To <em>Top Whisker Tonic</em></h2>
<p class="intro">We are a global business with the mission is to curate all available beard oils from around the world, review &amp; grade them &amp; present this curated collection to the users of the site. Our Target Audience are all grooming men. Lorem ipsum dolor sit amet, consectetuer adipiscing elit, sed diam nonummy nibh euismod tincidunt ut laoreet dolore magna aliquam erat volutpat. Lorem ipsum dolor sit amet, consectetuer adipiscing elit, sed diam nonummy nibh euismod tincidunt ut laoreet dolore magna aliquam erat volutpat.</p>

<section class="process">
  <svg class="connectors" width="1200" height="120" viewBox="0 0 1200 120">
    <path id="arcA" d="M285 70 Q420 110 545 60" fill="none" stroke="#6b0f0f" stroke-width="1.5" stroke-dasharray="2 4"/>
    <path id="arcB" d="M655 30 Q790 -10 920 55" fill="none" stroke="#6b0f0f" stroke-width="1.5" stroke-dasharray="2 4"/>
    <text font-family="Raleway,sans-serif" font-size="13" fill="#6b0f0f" dy="-6"><textPath href="#arcA" startOffset="10%">We curate all available beard oils</textPath></text>
    <text font-family="Raleway,sans-serif" font-size="13" fill="#6b0f0f" dy="-6"><textPath href="#arcB" startOffset="8%">Review &amp; Grade them &amp; Present</textPath></text>
  </svg>
  <div class="step" style="left:172px">
    <div class="step-circle"><svg width="50" height="50" viewBox="0 0 24 24"><path d="M4 12l5 5L20 6" fill="none" stroke="#6b0f0f" stroke-width="3"/></svg></div>
    <div class="step-label display">Curate</div>
  </div>
  <div class="step" style="left:545px">
    <div class="step-circle"><svg width="52" height="52" viewBox="0 0 24 24"><path d="M12 2l3 6.5 7 .8-5.2 4.8 1.4 7L12 17.6 5.8 21l1.4-7L2 9.3l7-.8z" fill="#6b0f0f"/></svg></div>
    <div class="step-label display">Review &amp; Grade</div>
  </div>
  <div class="step" style="left:918px">
    <div class="step-circle"><svg width="50" height="50" viewBox="0 0 24 24"><rect x="3" y="4" width="18" height="14" rx="1" fill="none" stroke="#6b0f0f" stroke-width="2"/><path d="M3 8h18" stroke="#6b0f0f" stroke-width="2"/><path d="M12 20v-8m-3 3l3-3 3 3" fill="none" stroke="#6b0f0f" stroke-width="2"/></svg></div>
    <div class="step-label display">Present</div>
  </div>
</section>

<table class="reviews">
  <colgroup><col style="width:190px"><col style="width:71px"><col style="width:91px"><col style="width:102px"><col style="width:60px"><col style="width:60px"><col style="width:60px"><col style="width:52px"><col style="width:95px"></colgroup>
  <thead><tr>
    <th class="dark">Product, Supplier</th><th class="dark">Origin ▾</th><th class="dark">Base Oil ▾</th><th class="dark">Scent ▾</th>
    <th class="light">Aroma ▾</th><th class="light">Thera. ▾ Affect</th><th class="light">Value ▾</th><th class="light">Over ▾ All</th><th class="light">Get It</th>
  </tr></thead>
  <tbody>
    <tr><td class="product"><div class="product-cell"><span class="thumb"></span><div><div class="p-name">Trail-Ranger</div><div class="p-maker">-Bristle Brothers</div></div></div></td><td>USA</td><td>Jojoba, Hempseed</td><td>Spice Market</td><td>5</td><td>5</td><td>5</td><td>5</td><td><span class="buy">Buy Now</span></td></tr>
    <tr><td class="product"><div class="product-cell"><span class="thumb dark"></span><div><div class="p-name">Harbor Cask Tobacco</div><div class="p-maker">-Bristle Brothers</div></div></div></td><td>USA</td><td>Jojoba, Hempseed</td><td>Spice Market</td><td>5</td><td>5</td><td>5</td><td>5</td><td><span class="buy">Buy Now</span></td></tr>
    <tr><td class="product"><div class="product-cell"><span class="thumb"></span><div><div class="p-name">Trail-Ranger</div><div class="p-maker">-Bristle Brothers</div></div></div></td><td>USA</td><td>Jojoba, Hempseed</td><td>Spice Market</td><td>5</td><td>5</td><td>5</td><td>5</td><td><span class="buy">Buy Now</span></td></tr>
    <tr><td class="product"><div class="product-cell"><span class="thumb dark"></span><div><div class="p-name">Harbor Cask Tobacco</div><div class="p-maker">-Bristle Brothers</div></div></div></td><td>USA</td><td>Jojoba, Hempseed</td><td>Spice Market</td><td>5</td><td>5</td><td>5</td><td>5</td><td><span class="buy">Buy Now</span></td></tr>
    <tr><td class="product"><div class="product-cell"><span class="thumb"></span><div><div class="p-name">Trail-Ranger</div><div class="p-maker">-Bristle Brothers</div></div></div></td><td>USA</td><td>Jojoba, Hempseed</td><td>Spice Market</td><td>5</td><td>5</td><td>5</td><td>5</td><td><span class="buy">Buy Now</span></td></tr>
    <tr><td class="product"><div class="product-cell"><span class="thumb dark"></span><div><div class="p-name">Harbor Cask Tobacco</div><div class="p-maker">-Bristle Brothers</div></div></div></td><td>USA</td><td>Jojoba, Hempseed</td><td>Spice Market</td><td>5</td><td>5</td><td>5</td><td>5</td><td><span class="buy">Buy Now</span></td></tr>
    <tr><td class="product"><div class="product-cell"><span class="thumb"></span><div><div class="p-name">Trail-Ranger</div><div class="p-maker">-Bristle Brothers</div></div></div></td><td>USA</td><td>Jojoba, Hempseed</td><td>Spice Market</td><td>5</td><td>5</td><td>5</td><td>5</td><td><span class="buy">Buy Now</span></td></tr>
    <tr><td class="product"><div class="product-cell"><span class="thumb dark"></span><div><div class="p-name">Harbor Cask Tobacco</div><div class="p-maker">-Bristle Brothers</div></div></div></td><td>USA</td><td>Jojoba, Hempseed</td><td>Spice Market</td><td>5</td><td>5</td><td>5</td><td>5</td><td><span class="buy">Buy Now</span></td></tr>
    <tr><td class="product"><div class="product-cell"><span class="thumb"></span><div><div class="p-name">Trail-Ranger</div><div class="p-maker">-Bristle Brothers</div></div></div></td><td>USA</td><td>Jojoba, Hempseed</td><td>Spice Market</td><td>5</td><td>5</td><td>5</td><td>5</td><td><span class="buy">Buy Now</span></td></tr>
    <tr><td class="product"><div class="product-cell"><span class="thumb dark"></span><div><div class="p-name">Harbor Cask Tobacco</div><div class="p-maker">-Bristle Brothers</div></div></div></td><td>USA</td><td>Jojoba, Hempseed</td><td>Spice Market</td><td>5</td><td>5</td><td>5</td><td>5</td><td><span class="buy">Buy Now</span></td></tr>
    <tr><td class="product"><div class="product-cell"><span class="thumb"></span><div><div class="p-name">Trail-Ranger</div><div class="p-maker">-Bristle Brothers</div></div></div></td><td>USA</td><td>Jojoba, Hempseed</td><td>Spice Market</td><td>5</td><td>5</td><td>5</td><td>5</td><td><span class="buy">Buy Now</span></td></tr>
    <tr><td class="product"><div class="product-cell"><span class="thumb dark"></span><div><div class="p-name">Harbor Cask Tobacco</div><div class="p-maker">-Bristle Brothers</div></div></div></td><td>USA</td><td>Jojoba, Hempseed</td><td>Spice Market</td><td>5</td><td>5</td><td>5</td><td>5</td><td><span class="buy">Buy Now</span></td></tr>
    <tr><td class="product"><div class="product-cell"><span class="thumb"></span><div><div class="p-name">Trail-Ranger</div><div class="p-maker">-Bristle Brothers</div></div></div></td><td>USA</td><td>Jojoba, Hempseed</td><td>Spice Market</td><td>5</td><td>5</td><td>5</td><td>5</td><td><span class="buy">Buy Now</span></td></tr>
    <tr><td class="product"><div class="product-cell"><span class="thumb dark"></span><div><div class="p-name">Harbor Cask Tobacco</div><div class="p-maker">-Bristle Brothers</div></div></div></td><td>USA</td><td>Jojoba, Hempseed</td><td>Spice Market</td><td>5</td><td>5</td><td>5</td><td>5</td><td><span class="buy">Buy Now</span></td></tr>
    <tr><td class="product"><div class="product-cell"><span class="thumb"></span><div><div class="p-name">Trail-Ranger</div><div class="p-maker">-Bristle Brothers</div></div></div></td><td>USA</td><td>Jojoba, Hempseed</td><td>Spice Market</td><td>5</td><td>5</td><td>5</td><td>5</td><td><span class="buy">Buy Now</span></td></tr>
  </tbody>
</table>
<div class="loading"><svg width="14" height="14" viewBox="0 0 24 24"><path d="M12 3a9 9 0 1 0 9 9" fill="none" stroke="#fff" stroke-width="3"/></svg>Loading More...</div>

<aside>
  <div class="signup-box">
    <h3 class="display">Get More Stuff Like<br>This In Your InBox</h3>
    <p>Subscribe to our mailing list &amp; get interesting stuff &amp; updates.</p>
    <div class="signup-input">Enter your email here</div>
    <div class="signup-btn">SIGNUP NOW</div>
    <p class="signup-note">We respect your privacy and take protecting it seriously</p>
  </div>
  <h3 class="blog-heading display">Latest Blog</h3>
  <article class="post" style="top:1450px">
    <div class="post-img" role="img" aria-label="Photo of a bearded man beside a beard oil bottle" style="background:linear-gradient(135deg,#4a4f55,#9aa3ab)"></div>
    <div class="post-title">How to Use Wren's Beard Oil</div><div class="post-date">February 12, 2016</div>
  </article>
  <article class="post" style="top:1711px">
    <div class="post-img" role="img" aria-label="Photo of herbs, spices and oil bottles on a table" style="background:linear-gradient(135deg,#8a6a3a,#c9a46a)"></div>
    <div class="post-title">How to Use Wren's Beard Oil</div><div class="post-date">February 12, 2016</div>
  </article>
  <article class="post" style="top:1960px">
    <div class="post-img" role="img" aria-label="Photo of a bearded man with a pipe outdoors" style="background:linear-gradient(135deg,#d9d2b8,#7a6a4a)"></div>
    <div class="post-title">How to Use Wren's Beard Oil</div><div class="post-date">February 12, 2016</div>
  </article>
  <article class="post" style="top:2211px">
    <div class="post-img" role="img" aria-label="Photo of a man trimming his beard" style="background:linear-gradient(135deg,#e6e8ea,#6fa8c8)"></div>
    <div class="post-title">How to Use Wren's Beard Oil</div><div class="post-date">February 12, 2016</div>
  </article>
</aside>

<footer class="footer">
  <span>Copyright 2016 Top Whisker Tonic. All Rights Reserved.</span>
  <div class="footer-social"><span></span><span></span><span></span><span></span></div>
</footer>
</body>
</html>
```